Velmor Spire Nine Flash website

we need a website to cater to 2 aspect of the business. We have Velmor spire residence and velmor spire office. For the office, we will get their inquire and arrange a face to face meetup to show them the office area for rent. For the residence side, it will need to be like staylane or roomvio.com. we want to allow them to book online for the date they need. We have a total of 10 different room configurations starting at $70 per night and up depending on the size of the room. example of the design is https://brisquelodge.com/

Target Market(s)

the website should have detail information on the layout, designs, and luxury of the building.

Industry/Entity Type

office and service appartment rental/lease

Coding

Coded - Design and coding required

Number of Pages Required

5+ page

Requirements
Must have
• a luxury perspective
Nice to have
• example https://brisquelodge.com/

```html
<!DOCTYPE html>
<html lang="en">
<head>
<meta charset="utf-8">
<title>Velmor Spire Nine</title>
<link href="https://fonts.googleapis.com/css2?family=Cinzel:wght@400;600&family=Lato:ital,wght@0,400;0,700;0,900;1,400&display=swap" rel="stylesheet">
<style>
:root{
  --gold:#c9952a;
  --gold-light:#e2b64a;
  --gold-dark:#9c6c17;
  --ink:#2a2a2a;
  --muted:#6f6a64;
  --cream:#f6f1ea;
  --stage:#9c9394;
  --night:#000;
  --white:#fff;
}
*{margin:0;padding:0;box-sizing:border-box}
html,body{width:1200px;height:3398px;overflow:hidden}
body{background:linear-gradient(180deg,#a39b9c,#948b8c);font-family:'Lato',sans-serif;color:var(--ink);position:relative}
.abs{position:absolute}
.screen{position:absolute;left:137px;width:926px;box-shadow:0 20px 50px rgba(0,0,0,.45);overflow:hidden}
.photo{position:absolute}
.serif{font-family:'Cinzel',serif}
.center{text-align:center}

/* splash */
.splash{top:121px;height:476px;background:linear-gradient(160deg,#3a342c,#1f1c18 55%,#2c261f)}
.splash-name{position:absolute;left:0;right:0;top:228px;text-align:center;font-family:'Cinzel',serif;font-size:30px;color:var(--gold);letter-spacing:1px}
.splash-btn{position:absolute;top:305px;height:50px;width:330px;border-radius:25px;font-weight:900;font-size:16px;display:flex;align-items:center;justify-content:center;letter-spacing:.2px}
.splash-btn.outline{left:127px;border:2px solid var(--gold);color:var(--gold-light)}
.splash-btn.solid{left:468px;background:var(--gold);color:var(--white)}

/* site */
.site{top:640px;height:2636px;background:var(--white)}
.topbar{position:absolute;left:0;top:0;width:100%;height:60px;background:var(--white);border-top:3px solid var(--gold);z-index:3}
.logo-disc{position:absolute;left:111px;top:-20px;width:150px;height:120px;border-radius:0 0 75px 75px;background:var(--white);z-index:4;display:flex;align-items:flex-end;justify-content:center;padding-bottom:42px}
.logo-word{font-family:'Cinzel',serif;color:var(--gold);font-size:13px;white-space:nowrap}
.nav{position:absolute;top:26px;left:315px;display:flex;gap:0;font-size:10px;font-weight:700;z-index:4}
.nav a{color:var(--ink);text-decoration:none;position:absolute;white-space:nowrap}
.nav a.active::after{content:"";position:absolute;left:0;right:0;bottom:-5px;height:2px;background:var(--gold)}
.enquire{position:absolute;left:707px;top:18px;z-index:4;line-height:1.15}
.enquire small{display:block;font-size:10px;font-weight:700}
.enquire b{font-size:14px;color:var(--gold)}
.ring{position:absolute;left:677px;top:20px;width:24px;height:24px;border:2px solid var(--gold);border-radius:50%;z-index:4}

.hero{position:absolute;left:0;top:60px;width:926px;height:405px;background:linear-gradient(150deg,#4a3f31,#2a241d 50%,#3b3226);clip-path:polygon(0 0,100% 0,100% 72%,96.8% 100%,3.2% 100%,0 72%)}
.hero h1{position:absolute;left:0;right:0;top:116px;text-align:center;font-family:'Cinzel',serif;font-weight:600;font-size:54px;color:var(--gold);letter-spacing:1px}
.btn{position:absolute;height:30px;background:linear-gradient(90deg,var(--gold-dark),var(--gold-light) 50%,var(--gold-dark));color:var(--white);font-size:11px;font-weight:700;display:flex;align-items:center;justify-content:center;clip-path:polygon(8% 0,100% 0,92% 100%,0 100%)}
.dots{position:absolute;top:420px;left:447px;display:flex;gap:9px}
.dots i{width:6px;height:6px;border-radius:50%;background:var(--white)}
.dots i.on{background:var(--gold-light)}

.section-title{position:absolute;left:0;right:0;text-align:center;font-family:'Cinzel',serif;font-size:38px;color:var(--gold);font-weight:400}
.band{position:absolute;background:#fbf8f3}

.arrow{position:absolute;width:34px;height:34px;border:1px solid #888;border-radius:50%;background:var(--white)}
.arrow svg{position:absolute;left:10px;top:9px}
.card{position:absolute;top:582px;width:168px}
.card .photo{position:relative;height:115px}
.card h3{font-size:14px;font-weight:400;margin-top:12px;color:var(--ink)}
.stars{color:var(--gold);font-size:10px;letter-spacing:2px}
.card p{font-size:10px;color:var(--muted);line-height:1.5;margin-top:3px}

.about{position:absolute;left:0;top:879px;width:926px;height:414px;background:var(--cream)}
.about h2{position:absolute;left:113px;top:75px;font-family:'Cinzel',serif;font-size:38px;color:var(--gold);font-weight:400}
.about p{position:absolute;left:113px;top:133px;width:370px;font-size:10.5px;line-height:1.72;color:var(--muted);text-align:justify}

.gallery-grid .photo{width:230px;height:185px}

.reviews{position:absolute;left:0;top:1900px;width:926px;height:322px;background:var(--cream)}
.review{position:absolute;top:112px;width:240px}
.avatar{position:absolute;left:0;top:0;width:52px;height:52px;border-radius:50%;border:3px solid var(--white);box-shadow:0 1px 4px rgba(0,0,0,.25)}
.review .quote{position:absolute;left:56px;top:0;width:170px;font-size:9px;font-style:italic;color:#999;line-height:1.65}
.review .quote b{color:var(--gold);font-size:14px;font-style:normal}
.review .who{position:absolute;left:56px;top:57px;font-size:8.5px;font-style:italic;color:var(--ink);line-height:1.4;white-space:nowrap}
.review .rate{position:absolute;left:56px;top:93px;color:var(--gold);font-size:12px;letter-spacing:2px}

.contact{position:absolute;left:0;top:2222px;width:926px;height:414px;background:var(--night);color:var(--white)}
.contact .section-title{top:50px}
.field{position:absolute;background:var(--white);color:#777;font-size:8px;padding:4px 10px}
.info{position:absolute;font-size:9px;line-height:1.45}
.icon-ring{position:absolute;width:26px;height:26px;border:2px solid var(--white);border-radius:50%}
.icon-ring svg{position:absolute;left:5px;top:5px}
.social{position:absolute;top:371px;width:21px;height:21px;border-radius:50%}
</style>
</head>
<body>

<!-- landing splash -->
<section class="screen splash" aria-label="Landing choice">
  <div class="photo" role="img" aria-label="Dim open-plan office interior with wooden ceiling slats and plants" style="inset:0;background:linear-gradient(160deg,rgba(70,62,50,.9),rgba(25,23,20,.95) 60%,rgba(48,42,35,.9))"></div>
  <div class="abs" style="left:433px;top:125px;width:60px;height:60px;border:2px solid var(--gold);border-radius:50%"></div>
  <div class="splash-name">Velmor Spire Nine</div>
  <div class="splash-btn outline">VELMOR SPIRE RESIDENCE</div>
  <div class="splash-btn solid">VELMOR SPIRE OFFICE</div>
</section>

<!-- home page -->
<main class="screen site">
  <header class="topbar">
    <nav class="nav">
      <a class="active" style="left:0">HOME</a>
      <a style="left:53px">ABOUT</a>
      <a style="left:112px">SERVICES</a>
      <a style="left:176px">LISTINGS</a>
      <a style="left:230px">NEWS</a>
      <a style="left:279px">CONTACT US</a>
    </nav>
    <div class="ring"><svg width="20" height="20" viewBox="0 0 20 20"><path d="M6 4l2 3-1.5 1.5a8 8 0 0 0 4 4L12 11l3 2-1 2.5C9 16 4 11 4.5 5.5z" fill="none" stroke="#c9952a" stroke-width="1.3"/></svg></div>
    <div class="enquire"><small>ENQUIRE US</small><b>+1 555 010 2040</b></div>
  </header>
  <div class="logo-disc"><span class="logo-word">Velmor Spire Nine</span></div>

  <section class="hero">
    <div class="photo" role="img" aria-label="Modern office interior with wooden slat ceiling and bookshelves" style="inset:0;background:linear-gradient(150deg,#51463a,#2a241d 50%,#3e3428)"></div>
    <h1>Velmor Spire Nine</h1>
    <div class="btn" style="left:410px;top:208px;width:106px">GET STARTED</div>
    <div class="dots"><i></i><i class="on"></i><i></i></div>
  </section>

  <!-- featured listings -->
  <div class="band" style="left:34px;top:470px;width:226px;height:409px"></div>
  <div class="band" style="left:563px;top:470px;width:130px;height:409px"></div>
  <div class="band" style="left:761px;top:470px;width:130px;height:409px"></div>
  <h2 class="section-title" style="top:510px">Featured Listings</h2>
  <div class="arrow" style="left:58px;top:622px"><svg width="12" height="14"><path d="M8 2L3 7l5 5" fill="none" stroke="#444" stroke-width="1.6"/></svg></div>
  <div class="arrow" style="left:833px;top:622px"><svg width="12" height="14"><path d="M4 2l5 5-5 5" fill="none" stroke="#444" stroke-width="1.6"/></svg></div>
  <article class="card" style="left:112px"><div class="photo" role="img" aria-label="Bright open office with white desks" style="background:linear-gradient(160deg,#e8ecef,#b9c2c8)"></div><h3>Sed ut perspiciatis</h3><div class="stars">★★★★★</div><p>Excepteur sint occaecat cupida tat non proidentsunt</p></article>
  <article class="card" style="left:290px"><div class="photo" role="img" aria-label="Industrial office with plants and brick walls" style="background:linear-gradient(160deg,#8a7a68,#3e3a36)"></div><h3>Sed ut perspiciatis</h3><div class="stars">★★★★★</div><p>Excepteur sint occaecat cupida tat non proidentsunt</p></article>
  <article class="card" style="left:468px"><div class="photo" role="img" aria-label="Glass-walled meeting office" style="background:linear-gradient(160deg,#c9ccce,#7f8589)"></div><h3>Sed ut perspiciatis</h3><div class="stars">★★★★★</div><p>Excepteur sint occaecat cupida tat non proidentsunt</p></article>
  <article class="card" style="left:646px"><div class="photo" role="img" aria-label="Warm lounge office with wooden tables" style="background:linear-gradient(160deg,#d9b98e,#9a7552)"></div><h3>Sed ut perspiciatis</h3><div class="stars">★★★★★</div><p>Excepteur sint occaecat cupida tat non proidentsunt</p></article>
  <div class="btn" style="left:385px;top:809px;width:156px">VIEW MORE LISTINGS</div>

  <!-- about -->
  <section class="about">
    <h2>About Us</h2>
    <p>Sed ut perspiciatis unde omnis iste natus error sit voluptatem accusantium doloremque laudantium, totam rem aperiam, eaque ipsa quae ab illo inventore veritatis et quasi architecto beatae vitae dicta sunt explicabo. Nemo enim ipsam voluptatem quia voluptas sit aspernatur aut odit aut fugit, sed quia consequuntur magni dolores eos qui ratione voluptatem sequi nesciunt. Neque porro quisquam est, qui dolorem ipsum quia dolor sit amet, consectetur, adipisci velit, sed quia non numquam eius modi tempora incidunt ut labore et dolore magnam aliquam quaerat voluptatem.</p>
    <div class="btn" style="left:113px;top:295px;width:115px">READ MORE</div>
    <div class="photo" role="img" aria-label="Team of four colleagues talking while seated on chairs" style="left:513px;top:62px;width:413px;height:290px;background:linear-gradient(160deg,#f1f0ee,#d8d2c9 60%,#b99a78)"></div>
  </section>

  <!-- gallery -->
  <div class="band" style="left:34px;top:1293px;width:226px;height:607px"></div>
  <div class="band" style="left:378px;top:1293px;width:130px;height:607px"></div>
  <div class="band" style="left:563px;top:1293px;width:130px;height:607px"></div>
  <div class="band" style="left:761px;top:1293px;width:130px;height:607px"></div>
  <h2 class="section-title" style="top:1355px">Our Gallery</h2>
  <div class="gallery-grid">
    <div class="photo" role="img" aria-label="White open-plan office" style="left:111px;top:1421px;background:linear-gradient(160deg,#e6e9eb,#9ea6ab)"></div>
    <div class="photo" role="img" aria-label="Loft office with brick and wood" style="left:348px;top:1421px;background:linear-gradient(160deg,#8b6a4c,#3a332c)"></div>
    <div class="photo" role="img" aria-label="Teal executive office with pendant lamp" style="left:586px;top:1421px;background:linear-gradient(160deg,#4a5f66,#2d3b40)"></div>
    <div class="photo" role="img" aria-label="Long office hall with dark ceiling" style="left:111px;top:1616px;background:linear-gradient(160deg,#4b4540,#b9b3ab)"></div>
    <div class="photo" role="img" aria-label="Office with dark feature wall and white desks" style="left:348px;top:1616px;background:linear-gradient(160deg,#3c4147,#cfd2d4)"></div>
    <div class="photo" role="img" aria-label="Office with green plants and wooden shelving" style="left:586px;top:1616px;background:linear-gradient(160deg,#9ba39c,#7d6c55)"></div>
    <div class="abs" style="left:454px;top:1505px;width:20px;height:20px;border-radius:50%;background:var(--gold);color:#fff;font-size:14px;line-height:20px;text-align:center">+</div>
  </div>
  <div class="btn" style="left:410px;top:1824px;width:106px">VIEW MORE</div>

  <!-- reviews -->
  <section class="reviews">
    <h2 class="section-title" style="top:60px">Customer Reviews</h2>
    <div class="arrow" style="left:52px;top:170px;width:24px;height:24px;border-color:#ccc;background:none"><svg width="12" height="14" style="left:5px;top:4px"><path d="M7 3L3 7l4 4" fill="none" stroke="#bbb" stroke-width="1.3"/></svg></div>
    <div class="arrow" style="left:850px;top:170px;width:24px;height:24px;border-color:#ccc;background:none"><svg width="12" height="14" style="left:6px;top:4px"><path d="M4 3l4 4-4 4" fill="none" stroke="#bbb" stroke-width="1.3"/></svg></div>
    <div class="review" style="left:101px">
      <div class="avatar" role="img" aria-label="Portrait of reviewer" style="background:linear-gradient(#c9b7a6,#8e7a6a)"></div>
      <p class="quote"><b>“</b> At vero eos et accusamus et iustodio dignissimos ducimus qui blanditiisprasent ium voluptatum deleniti atqu.</p>
      <p class="who">MAREN COLBY<br>Financial Services Professional</p>
      <div class="rate">★★★★☆</div>
    </div>
    <div class="review" style="left:353px">
      <div class="avatar" role="img" aria-label="Portrait of reviewer" style="background:linear-gradient(#b6b0aa,#6c6661)"></div>
      <p class="quote"><b>“</b> At vero eos et accusamus et iustodio dignissimos ducimus qui blanditiisprasent ium voluptatum deleniti atqu.</p>
      <p class="who">TALISE R. ORTEGA<br>National Urban Fellow at the Harborview</p>
      <div class="rate">★★★★☆</div>
    </div>
    <div class="review" style="left:603px">
      <div class="avatar" role="img" aria-label="Portrait of reviewer" style="background:linear-gradient(#cfcac5,#8a8580)"></div>
      <p class="quote"><b>“</b> At vero eos et accusamus et iustodio dignissimos ducimus qui blanditiisprasent ium voluptatum deleniti atqu.</p>
      <p class="who">JO PREWITT<br>Entrepreneur &amp; Upcoming</p>
      <div class="rate">★★★★☆</div>
    </div>
  </section>

  <!-- contact -->
  <footer class="contact">
    <h2 class="section-title">Contact Us</h2>
    <div class="abs" style="left:111px;top:112px;font-size:16px;font-weight:900">ENQUIRE NOW</div>
    <div class="field" style="left:111px;top:150px;width:154px;height:23px">Name :</div>
    <div class="field" style="left:273px;top:150px;width:153px;height:23px">Phone :</div>
    <div class="field" style="left:111px;top:182px;width:315px;height:22px">Email :</div>
    <div class="field" style="left:111px;top:212px;width:315px;height:51px">Message :</div>
    <div class="btn" style="left:113px;top:276px;width:90px">SUBMIT</div>

    <div class="abs" style="left:578px;top:120px;width:40px;height:40px;border:2px solid var(--gold);border-radius:50%"></div>
    <div class="abs serif" style="left:478px;top:188px;width:240px;text-align:center;color:var(--gold);font-size:17px">Velmor Spire Nine</div>

    <div class="icon-ring" style="left:520px;top:226px"><svg width="12" height="12" viewBox="0 0 12 12"><path d="M6 11S2 6.5 2 4.5a4 4 0 0 1 8 0C10 6.5 6 11 6 11z" fill="none" stroke="#fff" stroke-width="1.2"/><circle cx="6" cy="4.5" r="1.3" fill="#fff"/></svg></div>
    <div class="info" style="left:559px;top:228px">234 Velmor Spires<br>emo enim ipsam volem quia vol</div>
    <div class="icon-ring" style="left:705px;top:226px"><svg width="12" height="12" viewBox="0 0 12 12"><path d="M3 1.5l1.5 2.3-1 1a6 6 0 0 0 3 3l1-1 2.3 1.5-.8 1.9C5 10 2 7 1.8 2.3z" fill="#fff"/></svg></div>
    <div class="info" style="left:744px;top:235px">+1 555 010 2040</div>
    <div class="icon-ring" style="left:520px;top:260px"><svg width="12" height="12" viewBox="0 0 12 12"><rect x="1" y="2.5" width="10" height="7" fill="#fff"/><path d="M1 2.5l5 4 5-4" fill="none" stroke="#000" stroke-width="1"/></svg></div>
    <div class="info" style="left:559px;top:267px">info@velmorspires.com</div>

    <div class="abs" style="left:103px;top:338px;width:722px;height:1px;background:#333"></div>
    <div class="info" style="left:111px;top:376px;font-size:8.5px">Copyrights © 2024, Velmor Spires. All Rights Reserved. &nbsp;|&nbsp; Privacy policy</div>
    <div class="social" style="left:723px;background:#2f4b8f"></div>
    <div class="social" style="left:749px;background:#c23b33"></div>
    <div class="social" style="left:775px;background:#b08a5a"></div>
    <div class="social" style="left:801px;background:#1f74b0"></div>
  </footer>
</main>
</body>
</html>
```